Brivolt Technologies business card design

We need a business card designed with our new logo. it would be great if the card could communicate it is a technology based company.

Target Market(s)

system integrators

Industry/Entity Type

technology, IOT

Contact Information for Business Card

Name, designation, Address, telephone number, email address

Requirements
Must have
• logo and company name
Nice to have
• something to do with technology

```html
<!DOCTYPE html>
<html lang="en">
<head>
<meta charset="utf-8">
<title>Brivolt Technologies business card</title>
<link rel="stylesheet" href="https://fonts.googleapis.com/css2?family=Roboto:wght@400;500&display=swap">
<style>
  :root {
    --page: #f3f3f3;
    --card: #ffffff;
    --edge: #e2e2e2;
    --ink: #2b2b2b;
    --brand-dark: #3f4042;
    --accent: #f7931e;
  }
  * { box-sizing: border-box; margin: 0; padding: 0; }
  html, body { width: 1200px; height: 896px; overflow: hidden; }
  body {
    background: var(--page);
    font-family: "Roboto", Arial, sans-serif;
    color: var(--ink);
    position: relative;
  }
  .card {
    position: absolute;
    left: 334px;
    width: 527px;
    height: 302px;
    background: var(--card);
    border: 1px solid var(--edge);
    border-radius: 34px;
  }
  .card--front { top: 125px; }
  .card--back { top: 471px; }

  .brand {
    position: absolute;
    display: flex;
    align-items: center;
    color: var(--brand-dark);
    font-weight: 500;
    white-space: nowrap;
  }
  .brand__square { background: var(--accent); flex: none; }
  .card--front .brand {
    right: 261px;
    top: 138px;
    font-size: 15px;
    gap: 7px;
  }
  .card--front .brand__square { width: 12px; height: 12px; }
  .card--back .brand {
    left: 0; right: 0;
    justify-content: center;
    top: 124px;
    font-size: 38px;
    gap: 16px;
  }
  .card--back .brand__square { width: 30px; height: 30px; }

  .divider {
    position: absolute;
    left: 276px;
    top: 70px;
    width: 2px;
    height: 162px;
    background: var(--accent);
  }
  .details {
    position: absolute;
    left: 287px;
    top: 70px;
  }
  .details__name {
    color: var(--accent);
    font-weight: 500;
    font-size: 21px;
    line-height: 1;
    letter-spacing: 0.2px;
  }
  .details__role {
    font-size: 12px;
    margin-top: 5px;
  }
  .details__address {
    font-size: 12.5px;
    line-height: 21px;
    margin-top: 16px;
    font-style: normal;
  }
  .details__contacts {
    list-style: none;
    margin-top: 10px;
    font-size: 12.5px;
  }
  .details__contacts li {
    display: flex;
    align-items: center;
    gap: 3px;
    height: 20px;
  }
  .icon { width: 12px; height: 12px; fill: var(--accent); flex: none; }
</style>
</head>
<body>
  <section class="card card--front" aria-label="Card front">
    <div class="brand">
      <span class="brand__square"></span>
      <span class="brand__name">Brivolt Technologies</span>
    </div>
    <div class="divider"></div>
    <div class="details">
      <p class="details__name">DANIEL HARLOW</p>
      <p class="details__role">Managing Director</p>
      <address class="details__address">1840 Marlow Quay<br>Seabright CA 92711</address>
      <ul class="details__contacts">
        <li>
          <svg class="icon" viewBox="0 0 24 24" aria-hidden="true"><path d="M6.6 10.8a15.1 15.1 0 0 0 6.6 6.6l2.2-2.2a1 1 0 0 1 1-.25 11.4 11.4 0 0 0 3.6.57 1 1 0 0 1 1 1V20a1 1 0 0 1-1 1A17 17 0 0 1 3 4a1 1 0 0 1 1-1h3.5a1 1 0 0 1 1 1c0 1.25.2 2.45.57 3.57a1 1 0 0 1-.25 1z"/></svg>
          <span>555 214 0387</span>
        </li>
        <li>
          <svg class="icon" viewBox="0 0 24 24" aria-hidden="true"><path d="M2 5h20v14H2z M2 5l10 8 10-8" /><path d="M2 5l10 8 10-8" fill="none" stroke="#fff" stroke-width="1.6"/></svg>
          <span>hello@brivolt.tech</span>
        </li>
        <li>
          <svg class="icon" viewBox="0 0 24 24" aria-hidden="true"><circle cx="12" cy="12" r="10"/><path d="M2 12h20M12 2c3 3 3 17 0 20M12 2c-3 3-3 17 0 20" fill="none" stroke="#fff" stroke-width="1.4"/></svg>
          <span>www.brivolt.tech</span>
        </li>
      </ul>
    </div>
  </section>

  <section class="card card--back" aria-label="Card back">
    <div class="brand">
      <span class="brand__square"></span>
      <span class="brand__name">Brivolt Technologies</span>
    </div>
  </section>
</body>
</html>
```